Whitcombe Business Card Design

The name of the business is Dario Whitcombe, CPA LLC
The service that we offer is Accounting, Tax & Consulting Services. I need it to have the following items:
Dario Whitcombe, Principal
Phone Number
Email Address
Physical Address

I have attached the company logo, one in black and one in white. Please provide a design in black background and the other in white background. Please include "Accounting, Tax & Consulting Services". I want the business card to be clean and very professional.

```html
<!DOCTYPE html>
<html lang="en">
<head>
<meta charset="utf-8">
<title>Dario Whitcombe, CPA LLC — Business Card</title>
<link href="https://fonts.googleapis.com/css2?family=Montserrat:wght@600&family=Roboto:wght@400;500;700&display=swap" rel="stylesheet">
<style>
  :root {
    --backdrop: #d9d9d9;
    --brand-red: #9a161c;
    --deep-red: #641014;
    --ink: #444444;
    --ink-soft: #555555;
    --ink-muted: #777777;
    --paper: #ffffff;
  }
  * { margin: 0; padding: 0; box-sizing: border-box; }
  html, body { width: 1200px; height: 900px; overflow: hidden; }
  body {
    background: var(--backdrop);
    position: relative;
    font-family: "Roboto", Arial, sans-serif;
  }
  .card {
    position: absolute;
    left: 233px;
    width: 698px;
    height: 399px;
  }

  /* Front */
  .card-front {
    top: 43px;
    background: var(--brand-red);
    display: flex;
    flex-direction: column;
    align-items: center;
  }
  .front-mark {
    width: 70px;
    height: 70px;
    background: var(--deep-red);
    margin-top: 110px;
  }
  .front-name {
    margin-top: 42px;
    font-family: "Montserrat", Arial, sans-serif;
    font-weight: 600;
    font-size: 36px;
    color: var(--deep-red);
    letter-spacing: 0.5px;
    white-space: nowrap;
  }
  .front-descriptor {
    margin-top: 4px;
    font-family: "Montserrat", Arial, sans-serif;
    font-weight: 600;
    font-size: 26px;
    letter-spacing: 3px;
    color: var(--deep-red);
    white-space: nowrap;
  }

  /* Back */
  .card-back {
    top: 462px;
    background: var(--paper);
    overflow: hidden;
  }
  .back-brand {
    position: absolute;
    left: 35px;
    top: 31px;
    display: flex;
    align-items: center;
    gap: 10px;
  }
  .back-brand-square {
    width: 52px;
    height: 52px;
    background: var(--brand-red);
  }
  .back-brand-text { display: flex; flex-direction: column; }
  .back-brand-name {
    font-family: "Montserrat", Arial, sans-serif;
    font-weight: 600;
    font-size: 15px;
    color: var(--ink);
    white-space: nowrap;
  }
  .back-brand-descriptor {
    font-family: "Montserrat", Arial, sans-serif;
    font-weight: 600;
    font-size: 10.5px;
    letter-spacing: 1.2px;
    color: var(--ink-muted);
    white-space: nowrap;
    margin-top: 2px;
  }
  .holder {
    position: absolute;
    right: 28px;
    top: 27px;
    text-align: left;
  }
  .holder-name {
    font-weight: 500;
    font-size: 29px;
    color: var(--ink);
    line-height: 1.1;
    white-space: nowrap;
  }
  .holder-title {
    font-weight: 500;
    font-size: 21px;
    color: var(--brand-red);
    margin-top: 2px;
  }
  .contacts {
    position: absolute;
    left: 42px;
    top: 172px;
    list-style: none;
  }
  .contact {
    display: grid;
    grid-template-columns: 38px 130px 12px auto;
    align-items: start;
    font-size: 17px;
    line-height: 20px;
    color: var(--ink-soft);
    margin-bottom: 14px;
  }
  .contact svg { width: 22px; height: 22px; margin-top: -1px; }
  .contact-label { font-weight: 500; color: var(--ink); }
  .contact-value { white-space: nowrap; }
  .services-band {
    position: absolute;
    left: 0;
    bottom: 0;
    width: 100%;
    height: 48px;
    background: var(--brand-red);
    color: var(--paper);
    font-weight: 700;
    font-size: 22px;
    letter-spacing: 3px;
    text-align: center;
    line-height: 48px;
    white-space: nowrap;
  }
</style>
</head>
<body>

  <section class="card card-front">
    <div class="front-mark"></div>
    <div class="front-name">DARIO WHITCOMBE, CPA, LLC</div>
    <div class="front-descriptor">CERTIFIED PUBLIC ACCOUNTANT</div>
  </section>

  <section class="card card-back">
    <div class="back-brand">
      <div class="back-brand-square"></div>
      <div class="back-brand-text">
        <div class="back-brand-name">DARIO WHITCOMBE, CPA, LLC</div>
        <div class="back-brand-descriptor">CERTIFIED PUBLIC ACCOUNTANT</div>
      </div>
    </div>

    <div class="holder">
      <div class="holder-name">Dario Whitcombe</div>
      <div class="holder-title">Principal</div>
    </div>

    <ul class="contacts">
      <li class="contact">
        <svg viewBox="0 0 24 24" aria-hidden="true"><path fill="#9a161c" d="M6.6 10.8a15.2 15.2 0 0 0 6.6 6.6l2.2-2.2a1 1 0 0 1 1-.25 11.4 11.4 0 0 0 3.6.57 1 1 0 0 1 1 1V20a1 1 0 0 1-1 1A17 17 0 0 1 3 4a1 1 0 0 1 1-1h3.5a1 1 0 0 1 1 1c0 1.25.2 2.45.57 3.57a1 1 0 0 1-.25 1z"/></svg>
        <span class="contact-label">Office Phone</span>
        <span>:</span>
        <span class="contact-value">(480) 555-0142</span>
      </li>
      <li class="contact">
        <svg viewBox="0 0 24 24" aria-hidden="true"><rect x="2" y="5" width="20" height="14" fill="#9a161c"/><path d="M2 5l10 8 10-8M2 19l7-7M22 19l-7-7" stroke="#fff" stroke-width="1.6" fill="none"/></svg>
        <span class="contact-label">Email ID</span>
        <span>:</span>
        <span class="contact-value">info@whitcombecpa.com</span>
      </li>
      <li class="contact">
        <svg viewBox="0 0 24 24" aria-hidden="true"><path fill="#9a161c" d="M12 2a7 7 0 0 0-7 7c0 5.2 7 13 7 13s7-7.8 7-13a7 7 0 0 0-7-7zm0 9.5A2.5 2.5 0 1 1 12 6.5a2.5 2.5 0 0 1 0 5z"/></svg>
        <span class="contact-label">Address</span>
        <span>:</span>
        <span class="contact-value">421, Address line goes here<br>45552, Country Name</span>
      </li>
      <li class="contact">
        <svg viewBox="0 0 24 24" aria-hidden="true"><g fill="none" stroke="#9a161c" stroke-width="1.5"><circle cx="12" cy="12" r="10"/><ellipse cx="12" cy="12" rx="4.5" ry="10"/><path d="M2 12h20M4 7h16M4 17h16M12 2v20"/></g></svg>
        <span class="contact-label">Website</span>
        <span>:</span>
        <span class="contact-value">www.websitename.com</span>
      </li>
    </ul>

    <div class="services-band">ACCOUNTING, TAX &amp; CONSULTING SERVICES</div>
  </section>

</body>
</html>
```